Banner ads for LP that work with same theme as below banners

Love the banner ads below. Need more with attached photos. But use the same wording, font as in below banner ads. Should be LP size 1200/627 so I can use for Pixorly and LP. Looking for great ads to use as LP ads. We do lots of ads so it will be worth your time to enter this contest you will be rewarded with a ton of work. Need several banner ads that work together. So maybe 1 of the dresses, 1 of the sweater, 1 of the leggings, 1 of the jacket

Target Market(s)

Women 24-45

Industry/Entity Type

Fashion

Requirements
Must have
• Banner ads that work for LP and Pixorly
Nice to have
• Several options to choose from
Should not have
• not sure

```html
<!DOCTYPE html>
<html lang="en">
<head>
<meta charset="UTF-8">
<title>Winter Wear Collection Banner</title>
<link rel="stylesheet" href="https://fonts.googleapis.com/css2?family=Yellowtail&family=Tinos:wght@400;700&display=swap">
<style>
  :root {
    --sky-top: #2f7cc4;
    --sky-mid: #8cc2ea;
    --sky-low: #e6f1fa;
    --snow: #ffffff;
    --navy-text: #1c2438;
    --button-light: #e4e4e4;
    --button-dark: #9d9d9d;
    --button-text: #2f2f2f;
    --photo-hair: #a77a4f;
    --photo-jacket: #1f3457;
    --photo-knit: #bdbdbd;
  }
  * { margin: 0; padding: 0; box-sizing: border-box; }
  html, body {
    width: 1200px;
    height: 628px;
    overflow: hidden;
    background: var(--snow);
  }
  .banner {
    position: relative;
    width: 1200px;
    height: 628px;
    overflow: hidden;
    background: linear-gradient(180deg,
      var(--sky-top) 0%,
      var(--sky-mid) 24%,
      var(--sky-low) 48%,
      var(--snow) 62%,
      var(--snow) 100%);
  }
  .model-photo {
    position: absolute;
    left: 75px;
    top: 0;
    width: 450px;
    height: 628px;
    border-radius: 200px 200px 0 0;
    background:
      linear-gradient(180deg,
        rgba(167,122,79,0.85) 0%,
        rgba(167,122,79,0.6) 28%,
        rgba(31,52,87,0.95) 36%,
        var(--photo-jacket) 74%,
        var(--photo-knit) 80%,
        var(--photo-knit) 88%,
        #151515 90%,
        #151515 100%);
  }
  .headline-script {
    position: absolute;
    left: 578px;
    width: 500px;
    top: 72px;
    text-align: center;
    font-family: "Yellowtail", cursive;
    font-size: 64px;
    line-height: 1;
    color: var(--snow);
    letter-spacing: 3px;
  }
  .headline-caps {
    position: absolute;
    left: 578px;
    top: 163px;
    font-family: "Tinos", serif;
    font-size: 64px;
    line-height: 1;
    letter-spacing: 0.27em;
    color: var(--navy-text);
  }
  .shop-button {
    position: absolute;
    left: 668px;
    top: 335px;
    width: 386px;
    height: 54px;
    display: flex;
    align-items: center;
    justify-content: center;
    gap: 8px;
    background: linear-gradient(180deg, var(--button-light) 0%, #cfcfcf 45%, var(--button-dark) 100%);
    border: 1px solid #8a8a8a;
    font-family: "Tinos", serif;
    font-size: 35px;
    color: var(--button-text);
    text-transform: uppercase;
  }
  .shop-button strong { font-weight: 700; }
  .shop-button span { font-weight: 400; }
</style>
</head>
<body>
  <main class="banner">
    <div class="model-photo" role="img" aria-label="Photo of a woman with long wavy hair wearing a navy quilted puffer jacket with faux-fur collar and knit hem"></div>
    <h1 class="headline-script">Winter Wear</h1>
    <h2 class="headline-caps">COLLECTION</h2>
    <div class="shop-button"><strong>Shop</strong><span>the</span><strong>Look</strong></div>
  </main>
</body>
</html>
```